KORVEL Group Pty Ltd. Website and Domain

www.korvelgroup.com.au

require email addresses setup.

Info@korvelgroup.com.au
accounts@korvelgroup.com.au
peter.halloway@korvelgroup.com.au
grant.whitley@korvelgroup.com.au

Website should promote commercial and domestic electrical services, audio visual services and data and fibre installations.

similar to my mates site www.brisvane.com.au

Website needs to promote professionalism, electrical/electrician, audio visual and data/fibre cabling installations.

promote environmental friendly imaginary.

Coding

```html
<!DOCTYPE html>
<html lang="en">
<head>
<meta charset="utf-8">
<title>KORVEL Group Pty Ltd. — Electrical, Audio Visual, Data</title>
<link rel="stylesheet" href="https://fonts.googleapis.com/css2?family=Rubik:wght@400;500;600&family=Roboto:wght@400;500;700&display=swap">
<style>
:root{
  --green:#a6cf3a;
  --blue:#2b9fd9;
  --dark:#0d0d0f;
  --dark-2:#1b1b1e;
  --ink:#ffffff;
  --muted:#d7d7d7;
  --heading:'Rubik',sans-serif;
  --body:'Roboto',sans-serif;
}
*{margin:0;padding:0;box-sizing:border-box}
html,body{width:1200px;height:4796px;overflow:hidden}
body{position:relative;background:var(--dark);color:var(--ink);font-family:var(--body)}
.abs{position:absolute}
.btn{position:absolute;display:flex;align-items:center;justify-content:center;background:var(--green);color:#fff;font:500 15px/1 var(--heading);letter-spacing:1.5px;text-transform:uppercase;border:0}
.brand{position:absolute;display:flex;align-items:center;gap:14px;font:500 48px/1 var(--heading);color:var(--blue);letter-spacing:2px}
.brand .dot{width:58px;height:58px;border-radius:50%;border:4px solid var(--green)}
.section-title{position:absolute;left:0;width:1200px;display:flex;justify-content:center;align-items:center;gap:14px;font:500 40px/1 var(--heading);letter-spacing:3px;text-transform:uppercase;color:#fff}
.section-title .ring{width:64px;height:64px;border-radius:50%;border:5px solid var(--green);flex:none}
.photo{position:absolute}

/* hero */
.hero{position:absolute;left:0;top:0;width:1200px;height:650px;background:var(--dark-2);clip-path:polygon(0 0,100% 0,100% 86%,50% 100%,0 86%)}
.hero-photo{left:532px;top:0;width:668px;height:650px;background:linear-gradient(160deg,#e9e9ea 0%,#bfc3c6 35%,#7f8286 60%,#2c2d30 100%)}
.hero-shade{position:absolute;left:0;top:0;width:1200px;height:650px;background:linear-gradient(180deg,rgba(0,0,0,0) 60%,rgba(0,0,0,.55) 100%)}
.menu{left:813px;top:52px;font:400 18px/1 var(--heading);letter-spacing:2px;color:#fff}
.hero-title{left:87px;top:208px;font:600 62px/58px var(--heading);text-transform:uppercase;letter-spacing:1px}
.hero-sub{left:88px;top:338px;font:700 22px/1 var(--body);letter-spacing:.5px}

/* welcome */
.welcome-text{left:140px;top:850px;width:920px;text-align:center;font:400 15.5px/33px var(--body);color:#e8e8e8}

/* what we do */
.what{position:absolute;left:0;top:1116px;width:1200px;height:564px;background:var(--blue);clip-path:polygon(0 74px,40% 0,60% 0,100% 74px,100% 100%,0 100%)}
.tile{position:absolute;top:1312px;width:199px;height:223px}
.tile-label{position:absolute;top:1549px;width:205px;font:500 17px/23px var(--body);color:#fff}

/* services */
.svc-frame{position:absolute;border:0;background:var(--green)}
.svc-sub{font:500 27px/1 var(--heading);color:var(--blue);letter-spacing:1.5px;text-transform:uppercase}
.svc-title{font:500 31px/38px var(--heading);color:#fff;letter-spacing:2px;text-transform:uppercase;margin-top:8px}
.svc-text{font:400 15.5px/31.5px var(--body);color:#e0e0e0;text-align:justify;margin-top:24px}
.svc{position:absolute;width:542px}

/* gallery */
.gallery{position:absolute;left:0;top:3232px;width:1200px;height:705px;background:var(--green);clip-path:polygon(0 0,100% 0,100% 656px,50% 100%,0 656px)}
.g{position:absolute;width:214px;height:227px}

/* contact */
.contact{position:absolute;left:0;top:3880px;width:1200px;height:680px;background:radial-gradient(ellipse at 45% 25%,#2a2a2c 0%,#141416 55%,#0a0a0b 100%)}
.field{position:absolute;border:1.5px solid #cfcfcf;background:transparent;color:#fff;font:500 15px/1 var(--body);padding:14px 16px}

/* footer */
.foot-info{left:0;top:4712px;width:1200px;text-align:center;font:400 15px/1 var(--body);color:#fff}
.copy{left:0;top:4756px;width:1200px;text-align:center;font:400 12px/1 var(--body);color:#ddd}
</style>
</head>
<body>

<header class="hero">
  <div class="photo hero-photo" role="img" aria-label="Conference room with rows of chairs and a projector screen"></div>
  <div class="hero-shade"></div>
</header>
<div class="brand" style="left:90px;top:24px">
  <span class="dot"></span><span>KORVEL</span>
</div>
<div class="abs menu">MENU &#8964;</div>
<h1 class="abs hero-title">Complete Package<br>Solutions</h1>
<p class="abs hero-sub">ELECTRICAL . AUDIO VISUAL . DATA SERVICES</p>
<a class="btn" style="left:89px;top:394px;width:175px;height:43px">Get Started</a>
<svg class="abs" style="left:590px;top:608px" width="20" height="22" viewBox="0 0 20 22" aria-hidden="true">
  <path d="M3 3l7 7 7-7M3 11l7 7 7-7" fill="none" stroke="#9a9a9a" stroke-width="2"/>
</svg>

<section>
  <h2 class="section-title" style="top:738px"><span class="ring"></span>Welcome to KORVEL</h2>
  <p class="abs welcome-text">Lorem ipsum dolor sit amet, consectetur adipiscing elit, sed do eiusmod tempor incididunt ut labore et dolore magna aliqua. Ut enim ad minim veniam, quis nostrud exercitation ullamco laboris nisi ut aliquip ex ea commodo consequat. Duis aute irure dolor in reprehenderit in voluptate velit esse cillum dolore eu fugiat nulla pariatur.</p>
  <a class="btn" style="left:513px;top:980px;width:174px;height:42px">Read More</a>
</section>

<section class="what"></section>
<h2 class="section-title" style="top:1212px"><span class="ring"></span>What We Do</h2>
<div class="photo tile" style="left:88px;background:linear-gradient(150deg,#d9d4c9,#4a6da8 70%,#2c3f6e)" role="img" aria-label="Instructor teaching trainees with a multimeter"></div>
<div class="photo tile" style="left:294px;background:linear-gradient(150deg,#6b5b4a,#b58a5f 45%,#2d3140)" role="img" aria-label="Electrician wiring a switchboard"></div>
<div class="photo tile" style="left:500px;background:linear-gradient(150deg,#4c5a7a,#a7b0c4 50%,#23283a)" role="img" aria-label="Microphone on an audio mixing desk"></div>
<div class="photo tile" style="left:705px;background:linear-gradient(150deg,#2a2d3a,#d7b94a 40%,#7bc0a8 70%,#e06fa0)" role="img" aria-label="Bundle of fibre optic cables"></div>
<div class="photo tile" style="left:911px;background:linear-gradient(150deg,#e6e6e2,#c8b36a 45%,#5b6a3a)" role="img" aria-label="Smiling electrician in hard hat at a panel"></div>
<p class="tile-label" style="left:88px">Promote<br>Professionalism</p>
<p class="tile-label" style="left:294px">Electrical/<br>electrician</p>
<p class="tile-label" style="left:500px">Audio Visual</p>
<p class="tile-label" style="left:705px">Data/fibre Cabling<br>Installations</p>
<p class="tile-label" style="left:911px">Promote Environmentally<br>Friendly Imagery</p>

<section>
  <h2 class="section-title" style="top:1754px"><span class="ring"></span>Our Main Services</h2>

  <div class="svc-frame" style="left:99px;top:1878px;width:428px;height:361px"></div>
  <div class="photo" style="left:89px;top:1868px;width:428px;height:361px;background:linear-gradient(170deg,#2e3560,#5a4a8a 40%,#b23a5a 60%,#2ab2c9 85%,#1c2a3a)" role="img" aria-label="Modern house at dusk with lit pool"></div>
  <div class="svc" style="left:569px;top:1880px;width:542px">
    <p class="svc-sub">Commercial &amp; Domestic</p>
    <h3 class="svc-title">Electrical Services</h3>
    <p class="svc-text">Lorem ipsum dolor sit amet, consectetur adipiscing elit, sed do eiusmod tempor incididunt ut labore et dolore magna aliqua. Ut enim ad minim veniam, quis nostrud exercitation ullamco laboris nisi ut aliquip ex ea commodo consequat. Duis aute irure dolor in reprehenderit in voluptate velit esse cillum dolore eu fugiat nulla pariatur.</p>
  </div>
  <a class="btn" style="left:570px;top:2173px;width:175px;height:43px">Read More</a>

  <div class="svc" style="left:87px;top:2336px;width:540px">
    <p class="svc-sub">Commercial</p>
    <h3 class="svc-title">Audio Visual</h3>
    <p class="svc-text">Lorem ipsum dolor sit amet, consectetur adipiscing elit, sed do eiusmod tempor incididunt ut labore et dolore magna aliqua. Ut enim ad minim veniam, quis nostrud exercitation ullamco laboris nisi ut aliquip ex ea commodo consequat. Duis aute irure dolor in reprehenderit in voluptate velit esse cillum dolore eu fugiat nulla pariatur.</p>
  </div>
  <a class="btn" style="left:89px;top:2630px;width:175px;height:43px">Read More</a>
  <div class="svc-frame" style="left:682px;top:2334px;width:428px;height:361px"></div>
  <div class="photo" style="left:672px;top:2324px;width:428px;height:361px;background:linear-gradient(175deg,#5a5f6e,#3e5f8a 35%,#2a2c34 60%,#15161a)" role="img" aria-label="Microphone in front of a conference audience"></div>

  <div class="svc-frame" style="left:99px;top:2782px;width:428px;height:361px"></div>
  <div class="photo" style="left:89px;top:2772px;width:428px;height:361px;background:linear-gradient(100deg,#3a4a7a,#7d8fbf 35%,#2f5fb0 60%,#c8ccd6)" role="img" aria-label="Technician working on a network server rack"></div>
  <div class="svc" style="left:569px;top:2784px;width:542px">
    <p class="svc-sub">Commercial &amp; Domestic</p>
    <h3 class="svc-title">Data and Sustainable<br>Practices</h3>
    <p class="svc-text">Lorem ipsum dolor sit amet, consectetur adipiscing elit, sed do eiusmod tempor incididunt ut labore et dolore magna aliqua. Ut enim ad minim veniam, quis nostrud exercitation ullamco laboris nisi ut aliquip ex ea commodo consequat.</p>
  </div>
  <a class="btn" style="left:570px;top:3075px;width:175px;height:43px">Read More</a>
</section>

<section class="contact" role="img" aria-label="Dark photo of an electrician at work"></section>
<section class="gallery"></section>
<h2 class="section-title" style="top:3310px"><span class="ring"></span>Project Gallery</h2>
<div class="photo g" style="left:155px;top:3405px;background:linear-gradient(170deg,#8aa0b8,#d8c9a8 55%,#5b4a38)" role="img" aria-label="Lit suburban house at dusk"></div>
<div class="photo g" style="left:380px;top:3405px;background:linear-gradient(170deg,#1a2340,#3a3a48 50%,#c9954a 75%,#2a2420)" role="img" aria-label="House exterior lighting at night"></div>
<div class="photo g" style="left:606px;top:3405px;background:linear-gradient(160deg,#1d2c4a,#3b7ac2 55%,#0f1a2e)" role="img" aria-label="Stage camera and event screen"></div>
<div class="photo g" style="left:831px;top:3405px;background:linear-gradient(160deg,#d5d6d8,#6b6f77 50%,#1f2024)" role="img" aria-label="Gloved hand working on breaker panel"></div>
<div class="photo g" style="left:155px;top:3647px;background:linear-gradient(160deg,#9a9890,#b33a3a 50%,#3a3230)" role="img" aria-label="Technician repairing equipment"></div>
<div class="photo g" style="left:380px;top:3647px;background:linear-gradient(160deg,#f0efe9,#d9b35a 45%,#b07a5a)" role="img" aria-label="Electrician fitting a ceiling light"></div>
<div class="photo g" style="left:606px;top:3647px;background:linear-gradient(170deg,#e8ecf2,#c9ccd1 50%,#5a5f68)" role="img" aria-label="Hard hat and cable coils on a table"></div>
<div class="photo g" style="left:831px;top:3647px;background:linear-gradient(160deg,#0f3d7a,#3b8fd9 50%,#0c1e3a)" role="img" aria-label="Blue network patch cables"></div>

<section>
  <h2 class="section-title" style="top:4100px"><span class="ring"></span>Get In Touch</h2>
  <div class="field" style="left:162px;top:4199px;width:433px;height:45px">Name</div>
  <div class="field" style="left:605px;top:4199px;width:432px;height:45px">Email</div>
  <div class="field" style="left:162px;top:4255px;width:875px;height:100px">Message</div>
  <a class="btn" style="left:513px;top:4367px;width:174px;height:44px">Submit</a>
</section>

<footer>
  <div class="brand" style="left:458px;top:4612px;font-size:48px">
    <span class="dot"></span><span>KORVEL</span>
  </div>
  <p class="abs foot-info">
    <svg width="13" height="13" viewBox="0 0 24 24" aria-hidden="true" style="vertical-align:-1px"><path fill="#fff" d="M6.6 10.8a15 15 0 006.6 6.6l2.2-2.2c.3-.3.7-.4 1-.2 1.1.4 2.3.6 3.6.6.6 0 1 .4 1 1V20c0 .6-.4 1-1 1A17 17 0 013 4c0-.6.4-1 1-1h3.5c.6 0 1 .4 1 1 0 1.3.2 2.5.6 3.6.1.3 0 .7-.2 1z"/></svg>
    +61 7 3555 0142 &nbsp;|&nbsp;
    <svg width="14" height="11" viewBox="0 0 24 18" aria-hidden="true"><path fill="#fff" d="M0 0h24v18H0zM2 2v1l10 7 10-7V2z"/></svg>
    info@korvelgroup.com.au &nbsp;|&nbsp;
    <svg width="11" height="14" viewBox="0 0 18 24" aria-hidden="true" style="vertical-align:-1px"><path fill="#fff" d="M9 0a9 9 0 00-9 9c0 7 9 15 9 15s9-8 9-15a9 9 0 00-9-9zm0 12a3 3 0 110-6 3 3 0 010 6z"/></svg>
    18 Tarrant Lane, Brisvane QLD
  </p>
  <p class="abs copy">Copyright © 2020. KORVEL Group Pty Ltd. All Rights Reserved.</p>
</footer>

</body>
</html>
```